Website setup with Brightline (childtheme is velmora theme)

hey there, my name is tobias and i would need a website. Tundrix Framework, I use the velmora theme. I would like to say goodbye to the eye-catching website with a nice menu. I like to send you some example from websites I like. Https://harborquillnotes.com/about/ https://harborquillnotes.com The main tabs on the top should be "About", "Blog", "Video", "Resources" on the right / blog /

Number of Pages Required

1 page

Colors
0493ce
fbee3d
faa54b

```html
<!DOCTYPE html>
<html lang="en">
<head>
<meta charset="utf-8">
<title>Tobias Reed</title>
<link href="https://fonts.googleapis.com/css2?family=Open+Sans:wght@300;400;600;700&display=swap" rel="stylesheet">
<style>
:root{
  --ink:#1f1e27;
  --gold:#e5b92a;
  --paper:#ffffff;
  --mist:#f0f0f0;
  --card:#ececec;
  --text:#333333;
  --muted-dark:#9a9aa2;
  --pie-a:#e0580d;
  --pie-b:#e8800f;
  --pie-c:#f0a11c;
  --pie-d:#f3b535;
}
*{box-sizing:border-box;margin:0;padding:0}
html,body{width:1200px;height:4225px;overflow:hidden}
body{font-family:"Open Sans",Arial,sans-serif;color:var(--text);background:var(--paper);position:relative}
.section{position:absolute;left:0;width:1200px}
.abs{position:absolute}
.sec-title{position:absolute;left:0;width:1200px;text-align:center;font-weight:400;font-size:33px}

/* header */
.site-header{top:0;height:85px;background:var(--ink)}
.brand{left:132px;top:24px;font-weight:700;font-size:28px;color:var(--gold)}
.main-nav{right:132px;top:36px;display:flex;gap:30px;font-size:12px;color:#fff;text-transform:uppercase}
.main-nav .active{color:var(--gold)}

/* hero */
.hero{top:85px;height:529px;background:linear-gradient(90deg,#3b3b3b 0%,#555 45%,#666 70%,#4a4a4a 100%)}
.hero-photo{left:680px;top:0;width:340px;height:529px;background:radial-gradient(ellipse at 50% 45%,#c9c9c9 0%,#8d8d8d 45%,rgba(90,90,90,0) 75%)}
.hero h1{left:132px;top:150px;font-weight:300;font-size:52px;line-height:60px;color:#fff}
.hero .lead{left:132px;top:278px;font-size:14px;color:#e6e6e6}
.signup{left:132px;top:316px;width:516px;height:48px;background:#e4e4e4;border:2px solid #e4e4e4}
.signup span{position:absolute;left:20px;top:13px;font-size:14px;color:#444}
.signup .btn{position:absolute;right:0;top:0;width:122px;height:44px;background:var(--ink);color:var(--gold);font-size:14px;font-weight:600;text-align:center;line-height:44px;letter-spacing:.5px}
.slider-arrow{top:255px}

/* intro */
.intro{top:614px;height:301px}
.intro .body{left:177px;width:846px;top:132px;font-size:13px;line-height:21px;color:#666;text-align:center}
.read-more{font-size:13px;color:#333}
.intro .read-more{left:0;width:1200px;top:214px;text-align:center}

/* resources */
.resources{top:915px;height:615px;background:var(--ink);color:#fff}
.res-card{top:139px;width:288px}
.res-card .ph{height:186px}
.res-card h3{font-weight:400;font-size:17px;line-height:22px;margin-top:16px}
.res-card p{font-size:11px;line-height:15px;color:var(--muted-dark);margin-top:14px}
.outline-btn{width:104px;height:45px;border:1.5px solid var(--gold);color:#fff;font-size:14px;text-align:center;line-height:42px;text-transform:uppercase}

/* videos */
.videos{top:1530px;height:470px}
.videos .body{left:135px;width:930px;top:126px;font-size:13px;line-height:19px;color:#666;text-align:center}
.vid{top:200px;width:288px;height:188px}
.play{position:absolute;left:121px;top:71px}

/* income */
.income{top:2000px;height:600px;background:var(--mist)}
.income h2{left:132px;top:73px;font-weight:400;font-size:33px;color:var(--text)}
.income .body{left:132px;top:141px;width:430px;font-size:13px;line-height:19.5px;color:#555}
.feature{left:132px;top:318px;width:431px;height:76px;background:var(--ink)}
.feature strong{position:absolute;left:72px;top:17px;font-weight:600;font-size:16px;color:var(--gold)}
.feature small{position:absolute;left:72px;top:45px;font-size:10px;color:#bbb}
.legend{left:921px;top:170px;font-size:13px;color:#555}
.legend li{list-style:none;display:flex;align-items:center;height:38px}
.legend i{display:inline-block;width:30px;height:30px;margin-right:12px}
.timeline{left:132px;top:455px;width:936px;height:70px}
.years{position:absolute;top:36px;left:0;width:936px;font-size:20px;font-weight:600;color:#333}
.years span{position:absolute;width:80px;margin-left:-40px;text-align:center}

/* totals */
.totals{top:2600px;height:321px}
.total-card{top:133px;width:288px;height:112px;background:var(--card);padding:20px 22px}
.total-card h3{font-weight:600;font-size:15px;color:#222;margin-bottom:8px}
.total-card p{font-size:13px;line-height:19px;color:#333}

/* blog */
.blog{top:2921px;height:412px;background:var(--ink);color:#fff}
.post{top:152px;width:420px}
.post h3{font-weight:400;font-size:16px}
.post p{font-size:11px;line-height:15px;color:var(--muted-dark);margin-top:10px}
.post .read-more{display:block;color:#ccc;margin-top:14px;font-size:13px}

/* contact */
.contact{top:3333px;height:527px}
.field{height:45px;border:1px solid #ccc;font-size:12px;color:#555;padding:13px 14px;background:#fff}
.submit{left:552px;top:405px;width:96px;height:45px;background:var(--ink);color:#fff;font-size:14px;font-weight:600;text-align:center;line-height:45px}

/* footer */
.site-footer{top:3860px;height:365px;background:var(--ink);color:#ccc}
.site-footer .about p{font-size:11px;line-height:16px;color:#bbb;margin-bottom:16px}
.follow{left:637px;top:63px;font-size:14px;color:#ddd;display:flex;align-items:center;gap:9px}
.follow b{font-weight:400;margin-right:8px}
.follow i{display:inline-block;width:17px;height:17px;border-radius:50%;background:#888}
.footer-rule{left:132px;top:247px;width:936px;height:1px;background:#3c3b46}
.footer-nav{left:0;width:1200px;top:282px;text-align:center;font-size:12px;color:#ccc;word-spacing:4px}
.copyright{left:0;width:1200px;top:310px;text-align:center;font-size:11px;color:#999}
</style>
</head>
<body>

<header class="section site-header">
  <div class="abs brand">Tobias Reed</div>
  <nav class="abs main-nav">
    <span class="active">Home</span><span>About</span><span>Resources</span><span>Video</span><span>Blog</span><span>Contact</span>
  </nav>
</header>

<section class="section hero">
  <div class="abs hero-photo" role="img" aria-label="Smiling coach in a white shirt"></div>
  <h1 class="abs">I'm an Online Marketer,<br>Life and Business Coach</h1>
  <p class="abs lead">Pellentesque blandit lacus eget nunc faucibus, et tincidunt eros viverra.</p>
  <div class="abs signup"><span>Email Address</span><div class="btn">SUBSCRIBE</div></div>
  <svg class="abs slider-arrow" style="left:46px" width="14" height="22" viewBox="0 0 14 22"><path d="M11 3 3 11l8 8" fill="none" stroke="#fff" stroke-width="2.5"/></svg>
  <svg class="abs slider-arrow" style="left:1140px" width="14" height="22" viewBox="0 0 14 22"><path d="M3 3l8 8-8 8" fill="none" stroke="#fff" stroke-width="2.5"/></svg>
</section>

<section class="section intro">
  <h2 class="sec-title" style="top:70px;color:#222">Cras eget leo sed nunc hendrerit ultricies</h2>
  <p class="abs body">Maecenas vel tortor accumsan quam varius imperdiet vel eget elit. Aenean facilisis tincidunt lectus, id dictum nisl luctus eget. Vivamus efficitur ex condimentum, malesuada eros eget, feugiat nibh. Sed tellus ex, imperdiet eget gravida sit amet, volutpat eget turpis. In nec ultricies est. Etiam mattis augue vehicula odio posuere, sit amet tempus lectus luctus.</p>
  <p class="abs read-more">Read More &rarr;</p>
</section>

<section class="section resources">
  <h2 class="sec-title" style="top:70px">Resources</h2>
  <article class="abs res-card" style="left:132px">
    <div class="ph" role="img" aria-label="Hand pointing at a trading chart" style="background:linear-gradient(135deg,#6d5a3c,#2e3d3a 60%,#1b2a2e)"></div>
    <h3>Etiam vel massa elementum bibendum tellus venenatis feugiat</h3>
    <p>Aliquam erat volutpat. Quisque aliquet ex nec est vestibulum posuere. Pellentesque convallis maximus enim sit amet efficitur. Etiam id imperdiet lectus.</p>
  </article>
  <article class="abs res-card" style="left:456px">
    <div class="ph" role="img" aria-label="Hand touching a glowing new life screen" style="background:linear-gradient(135deg,#3c4f6e,#7d8ea6 50%,#2c3b55)"></div>
    <h3>Vivamus lacus justo, ultrices nec erat in, euismod iaculis mauris</h3>
    <p>Aliquam erat volutpat. Quisque aliquet ex nec est vestibulum posuere. Pellentesque convallis maximus enim sit amet efficitur. Etiam id imperdiet lectus.</p>
  </article>
  <article class="abs res-card" style="left:780px">
    <div class="ph" role="img" aria-label="Team planning with sticky notes" style="background:linear-gradient(135deg,#c79a62,#8a6a54 50%,#d9b37a)"></div>
    <h3>Aenean placerat, nibh vel accumsan aliquet, magna nibh accumsan.</h3>
    <p>Aliquam erat volutpat. Quisque aliquet ex nec est vestibulum posuere. Pellentesque convallis maximus enim sit amet efficitur. Etiam id imperdiet lectus.</p>
  </article>
  <div class="abs outline-btn" style="left:547px;top:491px">View All</div>
</section>

<section class="section videos">
  <h2 class="sec-title" style="top:70px;color:#222">Videos</h2>
  <p class="abs body">Proin a dolor mauris. Vestibulum ante ipsum primis in faucibus orci luctus et ultrices posuere cubilia Curae; Vestibulum eget nisl metus. Phasellus nisl est, condimentum vitae faucibus in, sollicitudin vel metus. Nunc sit amet consequat risus. Curabitur ac elit leo.</p>
  <div class="abs vid" style="left:132px;background:linear-gradient(135deg,#5b6d80,#b9c3cc 55%,#4c5866)" role="img" aria-label="Colleagues talking at a laptop">
    <svg class="play" width="46" height="46" viewBox="0 0 46 46"><circle cx="23" cy="23" r="22" fill="#fff"/><path d="M18 14l13 9-13 9z" fill="#333"/></svg></div>
  <div class="abs vid" style="left:456px;background:linear-gradient(135deg,#8d9298,#dfe2e4 55%,#5c6167)" role="img" aria-label="Desk with laptop and charts">
    <svg class="play" width="46" height="46" viewBox="0 0 46 46"><circle cx="23" cy="23" r="22" fill="#fff"/><path d="M18 14l13 9-13 9z" fill="#333"/></svg></div>
  <div class="abs vid" style="left:780px;background:linear-gradient(135deg,#9a8878,#d8cbbd 55%,#6e6258)" role="img" aria-label="People reviewing printed charts">
    <svg class="play" width="46" height="46" viewBox="0 0 46 46"><circle cx="23" cy="23" r="22" fill="#fff"/><path d="M18 14l13 9-13 9z" fill="#333"/></svg></div>
</section>

<section class="section income">
  <h2 class="abs">Our Monthly Income Reports</h2>
  <p class="abs body">Aenean sed quam non sapien faucibus consequat vitae sit amet orci. Praesent quis risus mi. In mollis nulla in pulvinar dictum. Vivamus interdum sagittis felis, ut dapibus ligula feugiat ac. In dictum sapien eu tellus finibus fermentum. Aenean faucibus lacus ut mollis commodo. Donec vestibulum odio sem, ac laoreet massa ullamcorper id. Donec molestie nisl et tellus hendrerit vehicula. Nunc eu ligula sed quam pulvinar maximus in vitae eros.</p>
  <div class="abs feature">
    <svg class="abs" style="left:20px;top:20px" width="36" height="36" viewBox="0 0 36 36"><circle cx="18" cy="18" r="17" fill="#fff"/><path d="M14 10l12 8-12 8z" fill="#1f1e27"/></svg>
    <strong>Integer massa lacinia lacinia nulla volutpat</strong>
    <small>Aenean sed quam non sapien faucibus</small>
  </div>
  <svg class="abs" style="left:614px;top:99px" width="282" height="282" viewBox="-141 -141 282 282" role="img" aria-label="Income breakdown pie chart">
    <path d="M0 0 0 -141 A141 141 0 1 1 -80.9 115.5Z" fill="var(--pie-a)"/>
    <path d="M0 0 -80.9 115.5 A141 141 0 0 1 -132.5 48.2Z" fill="var(--pie-b)"/>
    <path d="M0 0 -132.5 48.2 A141 141 0 0 1 -132.5 -48.2Z" fill="var(--pie-c)"/>
    <path d="M0 0 -132.5 -48.2 A141 141 0 0 1 0 -141Z" fill="var(--pie-d)"/>
  </svg>
  <ul class="abs legend">
    <li><i style="background:var(--pie-a)"></i>Donec vestibulum</li>
    <li><i style="background:var(--pie-b)"></i>Aenean feugiat</li>
    <li><i style="background:var(--pie-c)"></i>Donec molestie</li>
    <li><i style="background:var(--pie-d)"></i>Proin porta</li>
  </ul>
  <div class="abs timeline">
    <svg class="abs" style="left:0;top:8px" width="936" height="16" viewBox="0 0 936 16">
      <line x1="0" y1="8" x2="936" y2="8" stroke="#444" stroke-width="3"/>
      <circle cx="77" cy="8" r="7" fill="var(--gold)" stroke="#444" stroke-width="1.5"/>
      <circle cx="232" cy="8" r="6" fill="#222"/><circle cx="388" cy="8" r="6" fill="#222"/>
      <circle cx="543" cy="8" r="6" fill="#222"/><circle cx="699" cy="8" r="6" fill="#222"/>
      <circle cx="855" cy="8" r="6" fill="#222"/>
    </svg>
    <div class="years">
      <span style="left:77px;color:var(--gold)">2018</span><span style="left:232px">2017</span><span style="left:388px">2016</span>
      <span style="left:543px">2015</span><span style="left:699px">2014</span><span style="left:855px">2013</span>
    </div>
  </div>
</section>

<section class="section totals">
  <h2 class="sec-title" style="top:68px;color:#222">Nullam accumsan purus tempus</h2>
  <div class="abs total-card" style="left:132px"><h3>Total Income for 1st 365 days</h3><p>Gross Income : $54,548<br>Net Income : $15,842</p></div>
  <div class="abs total-card" style="left:456px"><h3>Total Income for 2017</h3><p>Gross Income : $58,985<br>Net Income : $17,952</p></div>
  <div class="abs total-card" style="left:780px"><h3>Total Income for 2016</h3><p>Gross Income : $65,487<br>Net Income : $22,412</p></div>
</section>

<section class="section blog">
  <h2 class="sec-title" style="top:78px">Blog</h2>
  <article class="abs post" style="left:132px">
    <h3>Mauris suscipit felis id nunc elementum varius</h3>
    <p>Praesent elementum nulla sit amet justo pellentesque scelerisque. Nam id tortor in ante iaculis porttitor in luctus mi. Vivamus gravida sem a pretium euismod. Nam lobortis, purus et fringilla tempus, risus arcu dignissim diam.</p>
    <span class="read-more">Read More &rarr;</span>
  </article>
  <article class="abs post" style="left:640px">
    <h3>Vestibulum facilisis dolor at purus tincidunt porta</h3>
    <p>Praesent elementum nulla sit amet justo pellentesque scelerisque. Nam id tortor in ante iaculis porttitor in luctus mi. Vivamus gravida sem a pretium euismod. Nam lobortis, purus et fringilla tempus, risus arcu dignissim diam.</p>
    <span class="read-more">Read More &rarr;</span>
  </article>
  <div class="abs outline-btn" style="left:547px;top:285px">View All</div>
</section>

<section class="section contact">
  <h2 class="sec-title" style="top:72px;color:#222">Contact</h2>
  <div class="abs field" style="left:248px;top:126px;width:344px">Full Name</div>
  <div class="abs field" style="left:609px;top:126px;width:343px">Email</div>
  <div class="abs field" style="left:248px;top:185px;width:344px">Phone</div>
  <div class="abs field" style="left:609px;top:185px;width:343px">Service For
    <svg class="abs" style="right:14px;top:19px" width="10" height="6" viewBox="0 0 10 6"><path d="M1 1l4 4 4-4" fill="none" stroke="#555" stroke-width="1.3"/></svg></div>
  <div class="abs field" style="left:248px;top:247px;width:704px;height:138px">Message</div>
  <div class="abs submit">SUBMIT</div>
</section>

<footer class="section site-footer">
  <div class="abs about" style="left:132px;top:61px;width:390px">
    <p>Fusce porta arcu ex, aliquet dictum nulla interdum quis. Donec quis ex semper, consequat ligula at, efficitur lacus. Phasellus elementum lacinia quam non scelerisque. Nulla malesuada sed sit amet turpis scelerisque maximus.</p>
    <p>Maecenas viverra iaculis efficitur. Nulla facilisi. Vestibulum pharetra diam eu, in posuere purus efficitur ac. Mauris placerat eros tortor, vel egestas mi mattis eget. Donec a nisi vel ante tristique mollis nec quis est. Praesent accumsan nunc a condimentum volutpat. Sed quis metus nibh.</p>
  </div>
  <div class="abs follow"><b>Follow us on :</b><i></i><i></i><i></i><i></i><i></i></div>
  <div class="abs" style="left:967px;top:62px;width:100px;height:100px;border-radius:50%;background:linear-gradient(180deg,#d9d9d9,#8a8a8a)" role="img" aria-label="Portrait of the coach"></div>
  <div class="abs footer-rule"></div>
  <p class="abs footer-nav">Home &nbsp;|&nbsp; About &nbsp;|&nbsp; Resources &nbsp;|&nbsp; Video &nbsp;|&nbsp; Blog &nbsp;|&nbsp; Contact</p>
  <p class="abs copyright">Copyright &copy; 2018 Tobias Reed. All rights reserved.</p>
</footer>

</body>
</html>
```